Business Card for Professional Photographer

I'm looking for an eye catching modern clean design that compliments my logo/ website fonts & colours.
I specialise in architecture, corporate & commercial photography so I'm marketing to professional clients rather than portrait / wedding clients.

I would prefer to not have a solid black design.

My logo brand guide is as follows :

Main front font. : Reislust
Main font colour : #fff
Slogan front font : Ubuntu Bold
Monogram front font : Venti Medium
Container colour : #fff

I need print ready files in pdf .png & .eps formats.

Included in the files below are some screen grabs as reference to font & colours etc.

```html
<!DOCTYPE html>
<html lang="en">
<head>
<meta charset="utf-8">
<title>Northlight Studio – Business Card</title>
<link rel="stylesheet" href="https://fonts.googleapis.com/css2?family=Mulish:wght@400;800&display=swap">
<style>
  :root {
    --stage: #3b332f;
    --gold-deep: #c4934f;
    --gold-mid: #dcbb74;
    --gold-light: #f4eba0;
    --paper: #ffffff;
    --ink: #4a4a4a;
    --white: #ffffff;
  }
  * { box-sizing: border-box; margin: 0; padding: 0; }
  html, body {
    width: 1200px;
    height: 716px;
    overflow: hidden;
    background: var(--stage);
    font-family: "Mulish", sans-serif;
  }
  .stage {
    position: relative;
    width: 1200px;
    height: 716px;
  }
  .card {
    position: absolute;
    top: 198px;
    width: 540px;
    height: 310px;
    border-radius: 2px;
    box-shadow: 0 18px 40px rgba(0,0,0,0.45);
    overflow: hidden;
  }
  /* Front */
  .card-front {
    left: 40px;
    background: linear-gradient(120deg, var(--gold-deep) 0%, var(--gold-mid) 50%, var(--gold-light) 100%);
  }
  .card-front .pattern-area {
    position: absolute;
    inset: 0;
    background: linear-gradient(120deg, rgba(255,255,255,0.04), rgba(255,255,255,0.10));
  }
  .front-brand {
    position: absolute;
    left: 84px;
    top: 118px;
    display: flex;
    align-items: center;
    gap: 16px;
    color: var(--white);
  }
  .brand-dot {
    width: 54px;
    height: 54px;
    border: 2px solid currentColor;
    border-radius: 50%;
  }
  .brand-text { display: flex; flex-direction: column; }
  .brand-name {
    font-size: 22px;
    font-weight: 400;
    letter-spacing: 4px;
    text-transform: uppercase;
  }
  .brand-tagline {
    font-size: 7px;
    letter-spacing: 2px;
    margin-top: 3px;
  }
  /* Back */
  .card-back {
    left: 620px;
    background: var(--paper);
  }
  .back-brand {
    position: absolute;
    right: 34px;
    top: 46px;
    display: flex;
    align-items: center;
    gap: 12px;
    color: var(--gold-deep);
  }
  .back-brand .brand-dot { width: 40px; height: 40px; border-color: var(--gold-mid); }
  .back-brand .brand-name { font-size: 16px; letter-spacing: 3px; }
  .back-brand .brand-tagline { font-size: 6px; color: var(--gold-mid); }
  .person {
    position: absolute;
    left: 34px;
    top: 150px;
  }
  .person-name {
    font-size: 24px;
    font-weight: 800;
    color: var(--gold-mid);
  }
  .person-role {
    font-size: 15px;
    color: var(--ink);
    margin-top: 2px;
  }
  .rule {
    position: absolute;
    left: 200px;
    right: 34px;
    top: 222px;
    height: 1px;
    background: linear-gradient(90deg, var(--gold-deep), var(--gold-light));
  }
  .contacts {
    position: absolute;
    left: 34px;
    right: 20px;
    top: 250px;
    display: flex;
    flex-wrap: wrap;
    gap: 4px 14px;
    font-size: 11px;
    color: var(--ink);
  }
  .contacts .label { color: var(--gold-mid); font-weight: 800; margin-right: 3px; }
</style>
</head>
<body>
<main class="stage">
  <section class="card card-front">
    <div class="pattern-area" role="img" aria-label="Faint repeating decorative pattern over gold gradient"></div>
    <div class="front-brand">
      <span class="brand-dot"></span>
      <div class="brand-text">
        <span class="brand-name">Northlight Studio</span>
        <span class="brand-tagline">Architecture Corporate Commercial</span>
      </div>
    </div>
  </section>

  <section class="card card-back">
    <div class="back-brand">
      <span class="brand-dot"></span>
      <div class="brand-text">
        <span class="brand-name">Northlight Studio</span>
        <span class="brand-tagline">Architecture Corporate Commercial</span>
      </div>
    </div>
    <div class="person">
      <p class="person-name">Laura Benning</p>
      <p class="person-role">Development Manager</p>
    </div>
    <div class="rule"></div>
    <div class="contacts">
      <span><span class="label">P :</span>0400 123 987</span>
      <span><span class="label">M :</span>laura@northlightstudio.com.au</span>
      <span><span class="label">W :</span>www.northlightstudio.com.au</span>
    </div>
  </section>
</main>
</body>
</html>
```